Kestrel Baseball & Softball Camp 2017

Design a flyer that will promote our 2017 summer camp for boys and girls softball.

Weeks of
July 10th - 14th
July 17th - 21st.

Players ages 5 - 11.
Full day = 9:30am - 2:30pm half day = 9:30am - 11:30am.
$295 / full day : $195/ half day

Hosted by "Kestrel Baseball" affiliated with the Harbor Comets Travel Baseball & Softball Club and the Maple Ridge Youth League,

Camp Location MRYL, Route 9C Birch Hollow.

PHone 555-240-7813, email info@kestrelball.example

The color should be "Red white and blue color scheme" with dates and location standing out. Kestrel Logo should be prominent MRYL and Comets smaller and secondary.

Feel free to use stock photo's if available. visit www.harborcomets.example for more pictures and there are links for the 2017 summer camp there with possibly some more information.

Target Market(s)

to catch the eye of parents of players ages 5 - 11 already at little league or shopping in local stores

Colors
ec1f27
0355a3
ffffff

Requirements
Must have
• red white and blue design,
• Kestrel logo and summer camp prominent so it catches the eye and explains what it is right away.
• the comets and maple ridge logo's a the bottom showing the affiliation.
Nice to have
• stock photo's or something showing players having a great time or a beautiful ballpark
Should not have
• to much clutter or hard to figure out what it's for

```html
<!DOCTYPE html>
<html lang="en">
<head>
<meta charset="utf-8">
<title>Kestrel Baseball &amp; Softball Summer Camp 2017</title>
<link href="https://fonts.googleapis.com/css2?family=Bebas+Neue&family=Oswald:wght@500;700&family=Kaushan+Script&display=swap" rel="stylesheet">
<style>
  :root {
    --red: #ec1f27;
    --blue: #0355a3;
    --navy: #1d3a6b;
    --white: #ffffff;
    --ink: #1b1b1b;
  }
  html, body { margin: 0; padding: 0; overflow: hidden; background: var(--white); }
  .flyer {
    position: relative; width: 819px; height: 1200px; overflow: hidden;
    background: var(--white); font-family: "Bebas Neue", "Oswald", sans-serif; color: var(--navy);
  }
  .flyer * { position: absolute; margin: 0; }
  .hero-photo {
    left: 0; top: 0; width: 819px; height: 520px;
    background: linear-gradient(160deg, #6f7d4a 0%, #8d9460 35%, #7a6f58 70%, #5b5a4a 100%);
  }
  .field-photo {
    left: 0; top: 440px; width: 819px; height: 520px;
    background: linear-gradient(180deg, #f1ece6 0%, #e6ddd2 55%, #d9cfc3 100%);
  }
  .waves { left: 0; top: 0; width: 819px; height: 1200px; }
  .brand-badge {
    left: 510px; top: 220px; width: 270px; height: 270px; border-radius: 50%;
    background: var(--white); display: flex; align-items: center; justify-content: center;
    box-shadow: 0 4px 14px rgba(0,0,0,.18);
  }
  .brand-name {
    position: static; font-family: "Bebas Neue", sans-serif; font-size: 58px;
    color: var(--red); letter-spacing: 1px; text-align: center; line-height: 1;
  }
  .kicker { left: 298px; top: 522px; font-size: 40px; letter-spacing: 9px; color: var(--red); }
  .title-script {
    left: 64px; top: 545px; font-family: "Kaushan Script", cursive; font-size: 112px;
    color: var(--red); line-height: 1.1; font-weight: 400;
  }
  .title-rule { left: 66px; top: 672px; width: 380px; height: 3px; background: var(--red); }
  .title-block {
    left: 446px; top: 572px; font-family: "Oswald", sans-serif; font-weight: 700;
    font-size: 98px; line-height: 1; color: var(--navy); letter-spacing: -1px;
  }
  .title-year {
    left: 664px; top: 590px; font-family: "Oswald", sans-serif; font-weight: 700;
    font-size: 40px; color: var(--red); transform: rotate(-90deg); transform-origin: center;
    width: 90px; text-align: center; line-height: 1;
  }
  .subtitle { left: 500px; top: 682px; font-family: "Kaushan Script", cursive; font-size: 30px; color: var(--navy); }
  .weeks-label { left: 96px; top: 688px; font-family: "Kaushan Script", cursive; font-size: 28px; color: var(--navy); }
  .week { left: 86px; font-size: 44px; color: var(--navy); line-height: 1; white-space: nowrap; }
  .week::before { content: "▸"; color: var(--red); font-size: 26px; margin-right: 10px; position: relative; top: -6px; }
  .week-1 { top: 724px; }
  .week-2 { top: 772px; }
  .ages-icon { left: 466px; top: 846px; width: 44px; height: 40px; }
  .ages-label { left: 522px; top: 832px; font-size: 40px; line-height: 0.95; color: var(--red); }
  .ages-disc {
    left: 634px; top: 790px; width: 154px; height: 154px; border-radius: 50%;
    background: var(--navy); color: var(--white); font-size: 52px;
    display: flex; align-items: center; justify-content: center;
  }
  .ages-disc span { position: static; }
  .clock-icon { left: 70px; top: 956px; width: 40px; height: 44px; }
  .schedule { left: 128px; top: 954px; font-size: 30px; line-height: 1; color: var(--navy); }
  .cost-label { left: 452px; top: 958px; font-family: "Kaushan Script", cursive; font-size: 28px; color: var(--navy); }
  .cost-icon {
    left: 530px; top: 964px; width: 36px; height: 36px; border-radius: 50%; background: var(--red);
    color: var(--white); font-family: "Oswald", sans-serif; font-weight: 700; font-size: 22px;
    display: flex; align-items: center; justify-content: center;
  }
  .cost-icon span { position: static; }
  .prices { left: 580px; top: 954px; font-size: 30px; line-height: 1; color: var(--navy); }
  .divider { left: 58px; top: 1040px; width: 712px; border-top: 3px dashed var(--ink); }
  .host-box { left: 58px; top: 1070px; width: 270px; height: 108px; border: 2px solid var(--ink); }
  .host-note {
    left: 8px; top: 6px; width: 254px; font-family: "Oswald", sans-serif; font-weight: 500;
    font-size: 9.5px; line-height: 1.35; color: var(--ink); text-transform: uppercase;
  }
  .partner-mark-a { left: 20px; top: 60px; width: 64px; height: 36px; background: var(--red); border-radius: 4px; }
  .partner-mark-b { left: 102px; top: 56px; width: 44px; height: 44px; background: #8dbf3f; border-radius: 50%; }
  .pin-icon { left: 372px; top: 1086px; width: 22px; height: 32px; }
  .phone-icon { left: 566px; top: 1086px; width: 20px; height: 32px; }
  .info-label { font-family: "Kaushan Script", cursive; font-size: 24px; color: var(--ink); top: 1084px; }
  .location-label { left: 404px; }
  .contact-label { left: 596px; }
  .info-text { top: 1122px; font-size: 20px; line-height: 1.2; color: var(--ink); }
  .location-text { left: 404px; }
  .contact-text { left: 596px; font-size: 18px; }
</style>
</head>
<body>
<main class="flyer">
  <div class="hero-photo" role="img" aria-label="Young player in a red batting helmet holding a bat on a grass field"></div>
  <div class="field-photo" role="img" aria-label="Softly focused infield dirt and chalk line"></div>

  <svg class="waves" viewBox="0 0 819 1200" aria-hidden="true">
    <path d="M0,470 C220,520 470,450 819,330 L819,420 C520,520 260,560 0,540 Z" fill="#f6f2ee"/>
    <path d="M0,430 C240,500 480,420 819,300 L819,345 C500,460 240,530 0,480 Z" fill="var(--red)"/>
    <path d="M0,420 C240,490 480,410 819,290 L819,302 C480,422 240,502 0,432 Z" fill="var(--navy)"/>
    <path d="M0,470 C240,540 490,460 819,345 L819,362 C490,478 240,560 0,490 Z" fill="var(--white)"/>
    <path d="M0,892 C300,892 430,760 819,712 L819,722 C430,770 300,902 0,902 Z" fill="var(--navy)"/>
    <path d="M0,902 C300,902 430,770 819,722 L819,762 C430,810 300,940 0,940 Z" fill="var(--red)"/>
    <path d="M0,938 C300,938 430,808 819,760 L819,1200 L0,1200 Z" fill="var(--white)"/>
  </svg>

  <div class="brand-badge"><p class="brand-name">Kestrel<br>Baseball</p></div>

  <p class="kicker">SOFTBALL</p>
  <h1 class="title-script">summer</h1>
  <div class="title-rule"></div>
  <p class="title-block">CAMP</p>
  <p class="title-year">2017</p>
  <p class="subtitle">for boys and girls</p>

  <p class="weeks-label">Weeks of</p>
  <p class="week week-1">JULY 10TH - 14TH</p>
  <p class="week week-2">JULY 17TH - 21ST.</p>

  <svg class="ages-icon" viewBox="0 0 44 40" aria-hidden="true">
    <circle cx="12" cy="6" r="5" fill="var(--red)"/><rect x="6" y="13" width="12" height="27" rx="3" fill="var(--red)"/>
    <circle cx="32" cy="6" r="5" fill="var(--red)"/><path d="M32,13 L42,32 L22,32 Z" fill="var(--red)"/><rect x="28" y="30" width="8" height="10" fill="var(--red)"/>
  </svg>
  <p class="ages-label">PLAYERS<br>AGES</p>
  <div class="ages-disc"><span>5 - 11</span></div>

  <svg class="clock-icon" viewBox="0 0 40 44" aria-hidden="true">
    <rect x="15" y="0" width="10" height="5" fill="var(--red)"/>
    <circle cx="20" cy="25" r="15" fill="none" stroke="var(--red)" stroke-width="5"/>
    <path d="M20,25 L20,16 M20,25 L27,29" stroke="var(--red)" stroke-width="3.5" stroke-linecap="round"/>
  </svg>
  <p class="schedule">FULL DAY 9:30AM - 2:30PM<br>HALF DAY 9:30AM - 11:30AM</p>

  <p class="cost-label">Cost:</p>
  <div class="cost-icon"><span>$</span></div>
  <p class="prices">$295 / FULL DAY<br>$195/ HALF DAY</p>

  <div class="divider"></div>

  <div class="host-box">
    <p class="host-note">Hosted by "Kestrel Baseball" affiliated with the Harbor Comets Travel Baseball &amp; Softball Club and the Maple Ridge Youth League.</p>
    <div class="partner-mark-a" aria-label="Harbor Comets badge"></div>
    <div class="partner-mark-b" aria-label="Maple Ridge Youth League badge"></div>
  </div>

  <svg class="pin-icon" viewBox="0 0 22 32" aria-hidden="true">
    <path d="M11,0 C5,0 0,5 0,11 C0,19 11,32 11,32 C11,32 22,19 22,11 C22,5 17,0 11,0 Z" fill="var(--ink)"/>
    <circle cx="11" cy="11" r="4" fill="var(--white)"/>
  </svg>
  <p class="info-label location-label">Camp Location:</p>
  <p class="info-text location-text">MRYL, ROUTE 9C<br>BIRCH HOLLOW.</p>

  <svg class="phone-icon" viewBox="0 0 20 32" aria-hidden="true">
    <rect x="0" y="0" width="20" height="32" rx="3" fill="var(--ink)"/>
    <rect x="3" y="4" width="14" height="20" fill="var(--white)"/>
    <circle cx="10" cy="28" r="2" fill="var(--white)"/>
  </svg>
  <p class="info-label contact-label">Contact:</p>
  <p class="info-text contact-text">PHONE 555-240-7813<br>EMAIL INFO@KESTRELBALL.EXAMPLE</p>
</main>
</body>
</html>
```